Woman owned consulting company needs an elegant and modern business card design

I need a business card design for my new consulting company, Mara Quillon Consulting. I am looking for something that is simple and elegant, but also creative and original. You can use either version of the logo that are attached. I have also included the information that needs to be featured on the business card.

Contact Information for Business Card

Requirements
Must have
• The logo and the font type and a standard business card size. Use shades of gray/silver and or rose gold that are in the logo.
• I didn't realize that my actual logo wasn't attached. Please incorporate in the designs.
Should not have
• Colors that are different from my logo

```html
<!DOCTYPE html>
<html lang="en">
<head>
<meta charset="utf-8">
<title>Mara Quillon Consulting — Business Card</title>
<link href="https://fonts.googleapis.com/css2?family=Cinzel:wght@400;500&display=swap" rel="stylesheet">
<style>
  :root{
    --backdrop:#8a8a8a;
    --card-light:#f2f2f3;
    --card-dark:#5e5e5e;
    --ink:#3f3f42;
    --ink-soft:#6b6b70;
    --silver:#a9a9ad;
    --silver-light:#d9d9dc;
  }
  *{margin:0;padding:0;box-sizing:border-box}
  html,body{width:1200px;height:1016px;overflow:hidden}
  body{background:var(--backdrop);position:relative;font-family:'Cinzel',serif}
  .card{position:absolute;left:332px;width:549px;box-shadow:0 8px 14px rgba(0,0,0,.28)}
  .card--front{top:146px;height:297px;background:var(--card-light);color:var(--ink)}
  .card--back{top:528px;height:313px;background:var(--card-dark);color:var(--silver)}

  .front__name{position:absolute;left:51px;top:44px;font-size:24px;font-weight:500;letter-spacing:.5px;line-height:1;white-space:nowrap}
  .front__title{position:absolute;left:53px;top:84px;font-size:10px;letter-spacing:14px;color:#77777b;line-height:1}
  .front__contact{position:absolute;left:51px;top:206px;list-style:none;font-size:12px;line-height:21px;white-space:nowrap}
  .front__mark{position:absolute;right:48px;top:212px;display:flex;align-items:center;gap:10px;color:var(--ink-soft)}
  .mark-dot{width:12px;height:12px;border-radius:50%;background:var(--ink-soft);flex:none}
  .mark-name{font-size:12px;letter-spacing:1px;line-height:18px;text-align:left;white-space:nowrap}

  .back__brand{position:absolute;left:0;right:0;top:108px;text-align:center;color:var(--silver-light)}
  .back__name{font-size:36px;letter-spacing:2px;line-height:1.1;white-space:nowrap}
  .back__sub{font-size:12px;letter-spacing:11px;margin-top:8px;color:var(--silver)}
  .back__web{position:absolute;left:0;right:0;top:246px;text-align:center;font-size:13px;letter-spacing:.5px;color:var(--silver);white-space:nowrap}
</style>
</head>
<body>
  <section class="card card--front">
    <h1 class="front__name">MARA QUILLON</h1>
    <p class="front__title">OWNER</p>
    <ul class="front__contact">
      <li>555-014-2273</li>
      <li>MARA@MARAQUILLONCONSULTING.COM</li>
      <li>WWW.MARAQUILLONCONSULTING.COM</li>
    </ul>
    <div class="front__mark">
      <span class="mark-dot"></span>
      <span class="mark-name">MARA QUILLON<br>CONSULTING</span>
    </div>
  </section>

  <section class="card card--back">
    <div class="back__brand">
      <p class="back__name">Mara Quillon</p>
      <p class="back__sub">CONSULTING</p>
    </div>
    <p class="back__web">WWW.MARAQUILLONCONSULTING.COM</p>
  </section>
</body>
</html>
```